GJ & DW Fencing Pty Ltd

We already have an existing logo created by Pixel Harbour however we have restructured to a company. We would like someone to add Pty Ltd to our business name please.

Colors

Designer to choose only greyscale colors for use in the design.

```html
<!DOCTYPE html>
<html lang="en">
<head>
<meta charset="utf-8">
<title>GJ &amp; DW Fencing Pty Ltd – Business Card</title>
<link rel="stylesheet" href="https://fonts.googleapis.com/css2?family=Lato:wght@400;900&display=swap">
<style>
  :root {
    --backdrop: #d9d9d9;
    --card: #000000;
    --ink: #ffffff;
    --shadow: rgba(0, 0, 0, 0.45);
  }
  html, body {
    margin: 0;
    padding: 0;
    width: 1200px;
    height: 900px;
    overflow: hidden;
    background: var(--backdrop);
  }
  .canvas {
    position: relative;
    width: 1200px;
    height: 900px;
  }
  .card {
    position: absolute;
    left: 330px;
    width: 556px;
    height: 344px;
    background: var(--card);
    color: var(--ink);
    box-shadow: 4px 5px 8px var(--shadow);
    font-family: "Lato", sans-serif;
  }
  .card--front { top: 90px; }
  .card--back { top: 470px; }

  .wordmark {
    position: absolute;
    font-family: "Lato", sans-serif;
    font-weight: 900;
    color: var(--ink);
    text-transform: uppercase;
    line-height: 1;
    text-align: right;
  }
  .wordmark__initials { display: block; font-size: 50px; letter-spacing: 1px; }
  .wordmark__trade { display: block; font-size: 22px; letter-spacing: 1px; margin-top: 6px; }
  .card--front .wordmark { right: 66px; top: 66px; }
  .card--back .wordmark {
    left: 0; right: 0; top: 120px; text-align: center;
  }

  .holder {
    position: absolute;
    left: 26px;
    top: 190px;
    margin: 0;
    font-size: 18px;
    font-weight: 900;
    letter-spacing: 0.5px;
  }
  .contacts {
    position: absolute;
    left: 26px;
    top: 226px;
    margin: 0;
    padding: 0;
    list-style: none;
    font-size: 16px;
  }
  .contacts li {
    display: flex;
    align-items: center;
    height: 24px;
    margin-bottom: 2px;
  }
  .contacts li.contacts__address { margin-top: 10px; }
  .contacts svg { width: 24px; height: 24px; margin-right: 6px; flex: none; }
</style>
</head>
<body>
<div class="canvas">

  <section class="card card--front">
    <div class="wordmark">
      <span class="wordmark__initials">GJ &amp; DW</span>
      <span class="wordmark__trade">Fencing Pty Ltd</span>
    </div>
    <h1 class="holder">RAY CALDER</h1>
    <ul class="contacts">
      <li>
        <svg viewBox="0 0 24 24" aria-hidden="true">
          <circle cx="12" cy="12" r="12" fill="#fff"/>
          <path d="M6.5 14.5h11v3h-11z M7.5 11.5q4.5-4 9 0l1 2h-11z" fill="#000"/>
          <circle cx="12" cy="15.8" r="1" fill="#fff"/>
        </svg>
        044 5218093
      </li>
      <li>
        <svg viewBox="0 0 24 24" aria-hidden="true">
          <circle cx="12" cy="12" r="12" fill="#fff"/>
          <rect x="6" y="8" width="12" height="8.5" fill="#000"/>
          <path d="M6.5 8.5l5.5 4.5 5.5-4.5" stroke="#fff" stroke-width="1.2" fill="none"/>
        </svg>
        gjdwfencing@mailpost.com
      </li>
      <li class="contacts__address">
        <svg viewBox="0 0 24 24" aria-hidden="true">
          <circle cx="12" cy="12" r="12" fill="#fff"/>
          <path d="M12 19c-3-4-5-6.5-5-9a5 5 0 0 1 10 0c0 2.5-2 5-5 9z" fill="#000"/>
          <circle cx="12" cy="10" r="2" fill="#fff"/>
        </svg>
        PO Box 418 Ridgevale WA 6390
      </li>
    </ul>
  </section>

  <section class="card card--back">
    <div class="wordmark">
      <span class="wordmark__initials">GJ &amp; DW</span>
      <span class="wordmark__trade">Fencing Pty Ltd</span>
    </div>
  </section>

</div>
</body>
</html>
```